Insurance Agency website design for Brellow Cover Insurance, LP

Build a website for Brellow Cover Insurance, LP which sells Homeowners, Auto, Renters, Condo, Flood, Disability, Life, Umbrella, and health insurance. We need the coolest insurance agency website out there to get quotes, contact us, or get additional information. Please list the following insurance companies we work with: Varnix, Ostle, Meridale Mutual, Quillor, Dunmarrow, KGZ, and Pellwick.

Make a design similar to https://www.fernagentry.com/

Selling personal insurance policies

```html
<!DOCTYPE html>
<html lang="en">
<head>
<meta charset="utf-8">
<title>Brellow Cover Insurance, LP</title>
<link href="https://fonts.googleapis.com/css2?family=Lexend:wght@400;500;600&family=Open+Sans:ital,wght@0,400;0,600;0,700;1,400&display=swap" rel="stylesheet">
<style>
:root{
  --blue:#1a6fba;
  --blue-deep:#0a6cc0;
  --navy:#123a6b;
  --footer:#1a3f8a;
  --green:#6cb33f;
  --text:#3a3f4a;
  --muted:#6b7380;
  --pale:#eaf1fb;
  --line:#d8e2ef;
  --white:#fff;
}
*{box-sizing:border-box;margin:0;padding:0}
html,body{width:1200px;height:4323px;overflow:hidden}
body{position:relative;font-family:"Open Sans",sans-serif;color:var(--text);background:var(--white)}
.abs{position:absolute}
h1,h2,h3,.head{font-family:"Lexend",sans-serif;font-weight:500}
.eyebrow{font-family:"Lexend",sans-serif;font-size:14px;letter-spacing:2px;color:var(--green);text-transform:uppercase}
.btn{display:inline-flex;align-items:center;justify-content:center;gap:8px;background:var(--green);color:#fff;border-radius:40px;font-family:"Lexend",sans-serif;font-size:14px;font-weight:600;text-transform:uppercase;letter-spacing:.5px}
.btn::after{content:"›";font-size:20px;line-height:1}

/* top bar */
.topbar{left:0;top:0;width:1200px;height:24px;background:var(--blue)}
.topbar span{position:absolute;top:4px;color:#fff;font-size:12px;font-weight:600}

/* hero */
.hero{left:0;top:24px;width:1200px;height:745px;background:linear-gradient(180deg,#eef3fb 0%,#dfe9f8 100%)}
.nav{left:87px;top:42px;width:1041px;height:87px;background:#fff;border-radius:20px;box-shadow:0 6px 24px rgba(30,80,150,.08)}
.brand{display:flex;align-items:center;gap:10px;font-family:"Lexend",sans-serif;font-weight:600;color:var(--blue);font-size:17px;line-height:1.1}
.brand .mark{width:34px;height:34px;border:3px solid var(--blue);border-radius:4px}
.nav .links{position:absolute;top:34px;font-family:"Lexend",sans-serif;font-size:13px;font-weight:600;color:var(--navy)}
.hero-tag{left:98px;top:230px;background:var(--green);color:#fff;font-family:"Lexend",sans-serif;font-size:16px;letter-spacing:1.5px;padding:4px 18px}
.hero p{left:98px;top:390px;width:500px;font-size:15.5px;line-height:23px}
.contact-row{display:flex;align-items:center;gap:10px;font-weight:600;color:var(--navy);font-size:16px}
.photo-ring{left:640px;top:172px;width:516px;height:516px;border-radius:50%;border:8px solid var(--green);border-left-color:transparent;border-bottom-color:transparent;transform:rotate(-20deg)}
.photo{left:650px;top:178px;width:496px;height:496px;border-radius:50%;background:radial-gradient(circle at 50% 40%,#e9e4dc,#b9a89a 70%,#8d7b6c);border:5px solid #fff}
.pill{background:#fff;border-radius:30px;padding:12px 22px;font-family:"Lexend",sans-serif;font-size:15px;font-weight:600;color:var(--navy);box-shadow:0 6px 20px rgba(0,0,0,.08);display:flex;gap:8px;align-items:center}
.pill.blue{background:var(--blue);color:#fff}

/* partners */
.partners{left:0;top:769px;width:1200px;height:115px;border-bottom:1px solid var(--line);display:flex;align-items:center;justify-content:space-around;padding:0 60px}
.partners span{font-family:"Lexend",sans-serif;font-size:24px;font-weight:500;color:var(--navy)}

/* about */
.about-img{left:107px;top:993px;width:463px;height:408px;border-radius:40px 0 40px 40px;background:linear-gradient(160deg,#d9ecfb 0%,#6fb2ea 60%,#3e86cf 100%)}
.badge{left:57px;top:1137px;width:148px;height:148px;border-radius:50%;background:#fff;border:2px dashed #9cc2e8;display:flex;flex-direction:column;align-items:center;justify-content:center;box-shadow:0 8px 20px rgba(0,0,0,.08)}
.badge b{font-family:"Lexend",sans-serif;font-size:32px;color:var(--blue);font-weight:600}
.badge small{font-family:"Lexend",sans-serif;font-size:14px;color:var(--green);font-weight:600}
.about h2{font-size:38px;line-height:46px;color:var(--blue)}
.about h2 span{color:var(--navy)}
.about p{font-size:15.5px;line-height:23px;margin-bottom:16px}

/* coverage */
.coverage{left:0;top:1530px;width:1200px;height:651px;background:linear-gradient(180deg,#eef3fb,#e4ecf8)}
.center{width:1200px;text-align:center}
.coverage h2{font-size:31px;line-height:42px;color:var(--blue)}
.coverage h2 span{color:var(--navy)}
.card{width:154px;height:128px;background:#fff;border-radius:8px;border:1px solid var(--line);box-shadow:0 4px 14px rgba(20,70,140,.07)}
.card::before{content:"";position:absolute;left:12px;top:12px;width:18px;height:18px;border:1px solid #cfd8e4;border-radius:3px;background:#f1f4f8}
.card svg{position:absolute;left:50px;top:30px;width:54px;height:50px}
.card span{position:absolute;left:0;top:92px;width:100%;text-align:center;font-size:15px;color:var(--blue)}

/* agent */
.agent h2{font-size:34px;line-height:47px;color:var(--blue)}
.agent h2 span{color:var(--navy)}
.agent-photo{left:75px;top:2391px;width:386px;height:386px;border-radius:50%;background:radial-gradient(circle at 50% 45%,#a9d98a,#6cb33f 70%);border:4px solid #fff;box-shadow:0 0 0 3px #cfe6c0}
.agent-card{left:601px;top:2262px;width:490px;height:448px;background:#fff;border:1px solid var(--line);border-radius:6px;box-shadow:0 8px 24px rgba(20,70,140,.08)}
.agent-card .head{height:126px;background:linear-gradient(90deg,#1a6fba,#0d5aa6);color:#fff;font-size:20px;line-height:27px;padding:22px 40px;font-family:"Open Sans",sans-serif;font-weight:400;border-radius:6px 6px 0 0}
.field{border:1px solid #b9c9de;border-radius:3px;height:48px;display:flex;align-items:center;gap:10px;padding:0 18px;font-size:14px;color:var(--muted);background:#fff}
.label{font-size:16px;color:var(--text)}

/* testimonials */
.testi{left:0;top:2786px;width:1200px;height:617px;background:linear-gradient(180deg,#fff 0%,#edf2f9 100%)}
.testi h2{font-size:33px;color:var(--blue)}
.testi h2 span{color:var(--navy)}
.tcard{width:317px;height:256px;background:#fff;border:1px solid var(--line);border-radius:4px;padding:28px 30px;box-shadow:0 4px 16px rgba(20,70,140,.06)}
.tcard .q{font-family:"Lexend",sans-serif;font-size:44px;color:#9cc2e8;line-height:30px;height:36px}
.tcard p{font-style:italic;font-size:13.5px;line-height:22px;color:#333}
.tcard .who{position:absolute;left:24px;bottom:28px;display:flex;gap:12px;align-items:center}
.avatar{width:38px;height:38px;border-radius:50%;background:#c9b6a6}
.who b{font-size:12px;display:block}
.stars{color:#f5a623;font-size:15px;letter-spacing:5px}
.gdot{position:absolute;right:26px;bottom:34px;width:24px;height:24px;border-radius:50%;background:#d6dde7}
.dots span{display:inline-block;width:42px;height:3px;background:#b8cde6;margin:0 10px}
.dots span:first-child{background:var(--blue)}

/* quote */
.footer-bg{left:0;top:3843px;width:1200px;height:480px;background:var(--footer)}
.quote{left:114px;top:3403px;width:1000px;height:515px;background:var(--blue-deep);border-radius:90px 0 90px 0;color:#fff}
.quote h2{font-size:34px;font-weight:600}
.quote p{font-size:15px;line-height:19.5px;margin-bottom:16px}
.qfield{background:#fff;height:48px;border-radius:2px;display:flex;align-items:center;gap:10px;padding:0 20px;color:#555;font-size:14px}

/* footer */
.fcol h4{font-family:"Lexend",sans-serif;font-size:15px;color:#fff;border-left:3px solid var(--green);padding-left:12px;margin-bottom:16px;letter-spacing:.5px}
.fcol a{display:block;color:#dbe6f7;font-size:13px;text-decoration:none;margin-bottom:12px;padding-left:24px}
.fdiv{width:1px;background:rgba(255,255,255,.15)}
.social span{display:inline-block;width:24px;height:24px;border-radius:50%;border:2px solid #fff;margin-right:20px}
.bottom{color:#cdd9ee;font-size:11px}
</style>
</head>
<body>

<div class="abs topbar"><span style="left:892px">Contact Us</span><span style="left:988px">Sign Up</span><span style="left:1070px">Log In</span></div>

<section class="abs hero" aria-label="Hero"></section>
<nav class="abs nav">
  <div class="brand abs" style="left:40px;top:20px"><span class="mark"></span><span>BRELLOW COVER<br><span style="color:var(--navy)">INSURANCE, LP</span></span></div>
  <span class="links" style="left:310px">GET INSURANCE ⌄</span>
  <span class="links" style="left:468px">PERSONAL ⌄</span>
  <span class="links" style="left:594px">WHY US</span>
  <span class="links" style="left:694px;font-size:15px;top:31px">
    <svg width="18" height="16" viewBox="0 0 24 24" style="vertical-align:-2px"><path fill="#6cb33f" d="M6.6 10.8a15 15 0 006.6 6.6l2.2-2.2c.3-.3.7-.4 1-.2 1.1.4 2.3.6 3.6.6.6 0 1 .4 1 1V20c0 .6-.4 1-1 1A17 17 0 013 4c0-.6.4-1 1-1h3.5c.6 0 1 .4 1 1 0 1.3.2 2.5.6 3.6.1.3 0 .7-.2 1z"/></svg>
    (555) 318-2046</span>
  <span class="btn abs" style="left:871px;top:23px;width:142px;height:41px;font-size:12px">Get a Quote</span>
</nav>

<div class="abs hero-tag">BRELLOW COVER INSURANCE LP</div>
<h1 class="abs" style="left:98px;top:264px;font-size:48px;line-height:52px;color:var(--blue);font-weight:600">Protecting What<br><span style="color:var(--navy)">Matters Most</span></h1>
<p class="abs" style="left:98px;top:390px;width:500px;font-size:15.5px;line-height:23px">At Brellow Cover Insurance, we understand that your peace of mind is invaluable. Our mission is to protect what matters most to you—your home, your vehicle, your health, and your loved ones. With our comprehensive range of insurance solutions, we are dedicated to safeguarding your assets and providing you with the security you deserve.</p>
<p class="abs" style="left:96px;top:544px;font-size:16px">For inquiries, please contact us at</p>
<div class="abs contact-row" style="left:98px;top:590px">
  <svg width="22" height="22" viewBox="0 0 24 24"><path fill="#1a6fba" d="M6.6 10.8a15 15 0 006.6 6.6l2.2-2.2c.3-.3.7-.4 1-.2 1.1.4 2.3.6 3.6.6.6 0 1 .4 1 1V20c0 .6-.4 1-1 1A17 17 0 013 4c0-.6.4-1 1-1h3.5c.6 0 1 .4 1 1 0 1.3.2 2.5.6 3.6.1.3 0 .7-.2 1z"/></svg>
  <span>(555) 318-2046</span>
  <svg width="22" height="18" viewBox="0 0 24 20" style="margin-left:20px"><rect x="1" y="2" width="22" height="16" rx="2" fill="#1a6fba"/><path d="M2 4l10 7 10-7" stroke="#fff" stroke-width="2" fill="none"/></svg>
  <span>info@BrellowCoverInsurance.com</span>
</div>

<div class="abs photo-ring"></div>
<div class="abs photo" role="img" aria-label="Smiling family of four sitting on a sofa, parents forming a roof shape with their arms"></div>
<div class="abs pill" style="left:613px;top:430px"><svg width="22" height="20" viewBox="0 0 24 22"><path d="M2 11L12 2l10 9M5 9v11h14V9" stroke="#6cb33f" stroke-width="2" fill="none"/></svg>Protect Home</div>
<div class="abs pill blue" style="left:1018px;top:397px"><svg width="24" height="20" viewBox="0 0 24 22"><path d="M12 20S2 13 2 7a5 5 0 0110-1 5 5 0 0110 1c0 6-10 13-10 13z" stroke="#fff" stroke-width="2" fill="none"/></svg>Your Health</div>
<div class="abs pill" style="left:910px;top:596px"><svg width="26" height="22" viewBox="0 0 26 22"><path d="M3 16h20l-2-6-4-4H8l-3 4z" stroke="#1a6fba" stroke-width="2" fill="none"/><circle cx="8" cy="17" r="2.5" fill="#1a6fba"/><circle cx="18" cy="17" r="2.5" fill="#1a6fba"/></svg>Protect Vehicle</div>

<div class="abs partners" aria-label="Carrier partners">
  <span>Varnix</span>
  <span>Ostle</span>
  <span>Meridale Mutual</span>
  <span>Quillor</span>
  <span>KGZ</span>
</div>

<section class="about">
  <div class="abs about-img" role="img" aria-label="Smiling man in glasses using a laptop in front of a city skyline"></div>
  <div class="abs badge"><b>20+</b><small>PRODUCTS</small></div>
  <div class="abs eyebrow" style="left:630px;top:957px">Who we are</div>
  <h2 class="abs" style="left:632px;top:978px">Brellow Cover<br><span>Insurance, LP</span></h2>
  <svg class="abs" style="left:920px;top:1042px" width="280" height="4"><line x1="0" y1="2" x2="280" y2="2" stroke="#1a6fba" stroke-width="2" stroke-dasharray="6 5"/></svg>
  <div class="abs" style="left:632px;top:1082px;width:530px">
    <p>Brellow Cover Insurance is a full-service, independent insurance agency with over three decades of experience in delivering comprehensive insurance solutions to individuals.</p>
    <p>We proudly offer a diverse portfolio of products from more than 20 of the most reputable and financially secure companies in the industry. Our dedicated team of over 50 skilled professionals is committed to customizing these products and services to meet the unique needs of each client.</p>
    <p>At Brellow Cover Insurance, our experts are focused on addressing the individual needs of our clients, ensuring exceptional service and support at every step</p>
  </div>
  <span class="abs btn" style="left:628px;top:1379px;width:174px;height:51px">Get a Quote</span>
  <svg class="abs" style="left:596px;top:1432px" width="116" height="100"><path d="M114 0v52H6v48" stroke="#1a6fba" stroke-width="2" stroke-dasharray="6 5" fill="none"/></svg>
</section>

<section class="abs coverage">
  <div class="abs center eyebrow" style="top:70px">Get started now</div>
  <h2 class="abs center" style="top:92px">Now more Specifically, what type of<br><span>Personal Protection are you looking for?</span></h2>
  <div class="abs center" style="top:195px;font-size:18px">Select up to three coverages</div>
</section>

<div class="abs card" style="left:247px;top:1770px"><svg viewBox="0 0 54 50"><path d="M4 32h46v-8l-6-4-8-8H16l-8 8-4 4z" stroke="#1a6fba" stroke-width="2" fill="none"/><circle cx="15" cy="33" r="5" stroke="#1a6fba" stroke-width="2" fill="#fff"/><circle cx="40" cy="33" r="5" stroke="#1a6fba" stroke-width="2" fill="#fff"/></svg><span>Auto</span></div>
<div class="abs card" style="left:431px;top:1770px"><svg viewBox="0 0 54 50"><path d="M8 24L27 6l19 18M12 20v24h30V20M22 44V32h10v12" stroke="#1a6fba" stroke-width="2" fill="none"/></svg><span>Home</span></div>
<div class="abs card" style="left:616px;top:1770px"><svg viewBox="0 0 54 50"><circle cx="34" cy="16" r="10" stroke="#1a6fba" stroke-width="2" fill="none"/><path d="M27 23L10 40l4 4 3-3 3 3 3-3-3-3 4-4" stroke="#1a6fba" stroke-width="2" fill="none"/></svg><span>Renters</span></div>
<div class="abs card" style="left:802px;top:1770px"><svg viewBox="0 0 54 50"><path d="M10 46V10h20v36M30 20h14v26M6 46h44" stroke="#1a6fba" stroke-width="2" fill="none"/><path d="M15 16h4M22 16h4M15 24h4M22 24h4M15 32h4M22 32h4M35 28h4M35 36h4" stroke="#1a6fba" stroke-width="2"/></svg><span>Condo</span></div>
<div class="abs card" style="left:247px;top:1921px"><svg viewBox="0 0 54 50"><path d="M6 24a21 18 0 0142 0zM27 6v-2M27 24v18" stroke="#1a6fba" stroke-width="2" fill="none"/><circle cx="16" cy="34" r="3" stroke="#1a6fba" stroke-width="2" fill="none"/><circle cx="38" cy="34" r="3" stroke="#1a6fba" stroke-width="2" fill="none"/><path d="M10 46a6 6 0 0112 0M32 46a6 6 0 0112 0" stroke="#1a6fba" stroke-width="2" fill="none"/></svg><span>Umbrella</span></div>
<div class="abs card" style="left:431px;top:1921px"><svg viewBox="0 0 54 50"><path d="M4 40h46M6 40V16l34-6 8 6v24M14 22h10v10H14zM30 22h10v18H30" stroke="#1a6fba" stroke-width="2" fill="none"/></svg><span>Mobile Home</span></div>
<div class="abs card" style="left:616px;top:1921px"><svg viewBox="0 0 54 50"><path d="M4 36V12h30v8h10l6 8v8zM10 18h8v8h-8zM22 18h8v8h-8z" stroke="#1a6fba" stroke-width="2" fill="none"/><circle cx="14" cy="38" r="4" stroke="#1a6fba" stroke-width="2" fill="#fff"/><circle cx="40" cy="38" r="4" stroke="#1a6fba" stroke-width="2" fill="#fff"/></svg><span>Motor Home</span></div>
<div class="abs card" style="left:802px;top:1921px"><svg viewBox="0 0 54 50"><circle cx="12" cy="34" r="8" stroke="#1a6fba" stroke-width="2" fill="none"/><circle cx="42" cy="34" r="8" stroke="#1a6fba" stroke-width="2" fill="none"/><path d="M12 34l8-14h14l8 14M22 20l4-8h8" stroke="#1a6fba" stroke-width="2" fill="none"/></svg><span>ATV</span></div>
<span class="abs btn" style="left:510px;top:2080px;width:172px;height:48px;font-size:12px">Show More</span>

<section class="agent">
  <svg class="abs" style="left:5px;top:2290px" width="100" height="4"><line x1="0" y1="2" x2="100" y2="2" stroke="#1a6fba" stroke-width="2" stroke-dasharray="6 5"/></svg>
  <div class="abs eyebrow" style="left:123px;top:2248px">Looking for agent</div>
  <h2 class="abs" style="left:123px;top:2268px">Find&nbsp; the right local<br><span>Agent for you</span></h2>
  <div class="abs agent-photo" role="img" aria-label="Smiling woman holding an open laptop in front of a green house background"></div>
  <svg class="abs" style="left:455px;top:2670px" width="200" height="100"><path d="M0 20c40 10 80 40 82 60s40 15 80-16" stroke="#1a6fba" stroke-width="1.5" stroke-dasharray="4 4" fill="none"/><path d="M156 60l10-8-2 14z" fill="#1a6fba"/></svg>
  <div class="abs agent-card">
    <div class="head">Just some basic information. The address of your personal property will help in finding the right local agent for you.</div>
    <div class="abs label" style="left:44px;top:158px">Enter the address of your insurable property</div>
    <div class="abs field" style="left:40px;top:192px;width:404px">✉ Email address</div>
    <div class="abs label" style="left:44px;top:258px">Zip code (require)</div>
    <div class="abs field" style="left:40px;top:288px;width:404px">● Type Zip code</div>
    <span class="abs btn" style="left:35px;top:358px;width:172px;height:46px">Next Step</span>
  </div>
</section>

<section class="abs testi">
  <svg class="abs" style="left:598px;top:26px" width="4" height="60"><line x1="2" y1="0" x2="2" y2="60" stroke="#1a6fba" stroke-width="2" stroke-dasharray="6 5"/></svg>
  <div class="abs center eyebrow" style="top:117px">Testimonials</div>
  <h2 class="abs center" style="top:140px"><span style="color:var(--blue)">What Our Client</span> <span>Says about us</span></h2>

  <div class="abs tcard" style="left:109px;top:218px"><div class="q">“</div><p>“Lorem ipsum dolor sit amet, consectetur adipiscing elit, sed do eiusmod tempor incididunt ut labore et dolore magna aliqua. Ut enim ad minim veniam, quis nostrud exercitation”</p><div class="who"><div class="avatar"></div><div><b>Talia Morrow</b><span class="stars">★★★★★</span></div></div><span class="gdot"></span></div>
  <div class="abs tcard" style="left:446px;top:218px"><div class="q">“</div><p>“Lorem ipsum dolor sit amet, consectetur adipiscing elit, sed do eiusmod tempor incididunt ut labore et dolore magna aliqua. Ut enim ad minim veniam, quis nostrud exercitation”</p><div class="who"><div class="avatar"></div><div><b>Talia Morrow</b><span class="stars">★★★★★</span></div></div><span class="gdot"></span></div>
  <div class="abs tcard" style="left:783px;top:218px"><div class="q">“</div><p>“Lorem ipsum dolor sit amet, consectetur adipiscing elit, sed do eiusmod tempor incididunt ut labore et dolore magna aliqua. Ut enim ad minim veniam, quis nostrud exercitation”</p><div class="who"><div class="avatar"></div><div><b>Talia Morrow</b><span class="stars">★★★★★</span></div></div><span class="gdot"></span></div>

  <div class="abs center dots" style="top:512px"><span></span><span></span><span></span></div>
  <svg class="abs" style="left:598px;top:560px" width="4" height="57"><line x1="2" y1="0" x2="2" y2="57" stroke="#1a6fba" stroke-width="2" stroke-dasharray="6 5"/></svg>
</section>

<div class="abs footer-bg"></div>
<section class="abs quote">
  <div class="abs eyebrow" style="left:76px;top:84px;color:#fff">Contact us</div>
  <h2 class="abs" style="left:76px;top:104px">Get a Quote</h2>
  <div class="abs" style="left:76px;top:166px;width:400px">
    <p>We believe that securing your home is one of the most important decisions you can make. Obtaining a comprehensive insurance quote is essential to understanding your coverage options and ensuring that your property is adequately protected against unforeseen events.</p>
    <p>Our team of experienced professionals is here to guide you through the process, helping you find the right policy that meets your specific needs and budget. Don't leave your home's safety to chance—get a quote today and take the first step towards peace of mind.</p>
  </div>
  <div class="abs qfield" style="left:536px;top:102px;width:402px">👤 Name</div>
  <div class="abs qfield" style="left:536px;top:162px;width:402px">✉ Email address</div>
  <div class="abs qfield" style="left:536px;top:222px;width:402px">☏ Phone</div>
  <div class="abs qfield" style="left:536px;top:282px;width:402px;height:90px;align-items:flex-start;padding-top:16px">💬 Message</div>
  <span class="abs btn" style="left:534px;top:388px;width:202px;height:46px">Send Message</span>
</section>

<footer>
  <div class="abs brand" style="left:140px;top:3990px;color:#fff"><span class="mark" style="border-color:#fff"></span><span>BRELLOW COVER<br>INSURANCE, LP</span></div>
  <p class="abs" style="left:140px;top:4052px;width:230px;color:#dbe6f7;font-size:11px;line-height:15px">Lorem ipsum dolor sit amet, consectetur adipiscing elit, sed do eiusmod tempor incididunt ut labore et dolore</p>
  <div class="abs social" style="left:143px;top:4126px"><span></span><span></span><span></span></div>
  <div class="abs fdiv" style="left:420px;top:3930px;height:300px"></div>
  <div class="abs fdiv" style="left:635px;top:3930px;height:300px"></div>
  <div class="abs fdiv" style="left:862px;top:3930px;height:300px"></div>
  <div class="abs fcol" style="left:418px;top:3994px"><h4>NAVIGATION</h4><a>Home</a><a>About Us</a><a>Insurance</a><a>Services</a><a>Testimonials</a></div>
  <div class="abs fcol" style="left:636px;top:3994px"><h4>INSURANCE</h4><a>Auto Insurance</a><a>Home Insurance</a><a>Life Insurance</a><a>Car Insurance</a><a>Business Insurance</a></div>
  <div class="abs fcol" style="left:860px;top:3994px"><h4>CONTACT US</h4>
    <a style="padding-left:54px;position:relative"><svg style="position:absolute;left:24px;top:0" width="18" height="18" viewBox="0 0 24 24"><path fill="#fff" d="M6.6 10.8a15 15 0 006.6 6.6l2.2-2.2c.3-.3.7-.4 1-.2 1.1.4 2.3.6 3.6.6.6 0 1 .4 1 1V20c0 .6-.4 1-1 1A17 17 0 013 4c0-.6.4-1 1-1h3.5c.6 0 1 .4 1 1 0 1.3.2 2.5.6 3.6.1.3 0 .7-.2 1z"/></svg>Phone Number<br>(555) 318-2046</a>
    <a style="padding-left:54px;position:relative;margin-top:16px"><svg style="position:absolute;left:24px;top:6px" width="18" height="14" viewBox="0 0 24 18"><rect x="1" y="1" width="22" height="16" rx="2" fill="#fff"/><path d="M2 3l10 7 10-7" stroke="#1a3f8a" stroke-width="2" fill="none"/></svg>Email address<br>info@BrellowCoverInsurance.com</a>
  </div>
  <div class="abs" style="left:0;top:4250px;width:1200px;height:1px;background:rgba(255,255,255,.12)"></div>
  <div class="abs bottom" style="left:137px;top:4274px">© 2025 Brellow Cover Insurance, LP.&nbsp; All Rights Reserved</div>
  <div class="abs bottom" style="left:908px;top:4268px">Terms of use&nbsp;&nbsp; Privacy Policy&nbsp;&nbsp; Sitemap</div>
</footer>

</body>
</html>
```